Alloy wheel repair business needs a website

Install logo previously purchased from makerhive, toolbar with dropdowns. services, gallery, clients , contact ect
Maybe mission statment

Target Market(s)

vehicle owners, auto dealers,insurance companies,

Industry/Entity Type

Alloy Wheel Repair

Coding

Coded - Design and coding required

Number of Pages Required

4 page

Font styles to use
Sans Serif

Colors
0054AA
0677BA
7BADD7
CADEEF
E8F1F8

```html
<!DOCTYPE html>
<html lang="en">
<head>
<meta charset="utf-8">
<title>Rimstone Wheelco – Wheel Repair Specialists</title>
<link href="https://fonts.googleapis.com/css2?family=Exo+2:ital,wght@0,600;0,800;1,700;1,800;1,900&family=Quicksand:wght@400;500;600;700&display=swap" rel="stylesheet">
<style>
:root{
  --blue:#0054AA;
  --blue-mid:#0677BA;
  --blue-soft:#7BADD7;
  --blue-pale:#CADEEF;
  --blue-mist:#E8F1F8;
  --ink:#1c2233;
  --dark:#232427;
  --text:#3b4150;
  --muted:#6c7280;
  --white:#ffffff;
  --star:#f2b01e;
}
*{box-sizing:border-box;margin:0;padding:0}
html,body{width:1200px;height:5056px;overflow:hidden}
body{position:relative;font-family:"Quicksand",sans-serif;color:var(--text);background:var(--white)}
.abs{position:absolute}
.heading{font-family:"Exo 2",sans-serif;font-style:italic;font-weight:900;letter-spacing:2px;text-transform:uppercase;color:var(--blue-mid);line-height:1.05}
.heading .dark{color:var(--ink)}
.eyebrow{font-family:"Exo 2",sans-serif;font-style:italic;font-weight:700;font-size:15px;letter-spacing:2px;text-transform:uppercase;color:var(--ink)}
.ghost-num{font-family:"Exo 2",sans-serif;font-style:italic;font-weight:800;font-size:92px;color:transparent;-webkit-text-stroke:1.5px var(--blue-pale);line-height:1}
.btn{display:inline-flex;align-items:center;gap:10px;font-family:"Quicksand",sans-serif;font-weight:700;font-size:17px;padding:0 30px;height:50px;color:var(--white);background:var(--blue);transform:skewX(-14deg);border-radius:4px;text-decoration:none}
.btn span{transform:skewX(14deg);display:inline-flex;align-items:center;gap:10px}
.btn.outline{background:transparent;color:var(--blue);border:2px solid var(--blue)}
p.body{font-size:17px;line-height:1.55;color:var(--text)}

/* header */
.site-header{left:0;top:0;width:1200px;height:80px;z-index:3}
.logo{left:88px;top:14px;font-family:"Exo 2",sans-serif;font-weight:800;font-size:30px;line-height:1;color:var(--blue);display:flex;align-items:center;gap:10px}
.logo .mark{width:34px;height:34px;border-radius:50%;background:var(--blue)}
.logo small{display:block;font-size:15px;letter-spacing:3px}
.main-nav{left:372px;top:22px;display:flex;gap:34px;font-weight:700;font-size:16px;color:var(--ink)}
.main-nav a{color:inherit;text-decoration:none}
.main-nav a.active{color:var(--blue-mid)}
.nav-phone{left:920px;top:12px;height:46px;font-size:16px}

/* hero */
.hero{left:0;top:0;width:1200px;height:720px;background:linear-gradient(180deg,#f4f5f7,#e9ebee);clip-path:polygon(0 0,100% 0,100% 92%,0 100%)}
.hero-title{left:88px;top:236px}
.hero-title .l1{font-size:40px}
.hero-title .l2{font-size:60px}
.hero-copy{left:88px;top:356px;width:440px}
.hero-cta{left:88px;top:424px}
.hero-wheel{left:600px;top:40px;width:540px;height:620px;border-radius:44px;background:linear-gradient(160deg,#c9ccd2 0%,#6f737b 45%,#2a2c31 100%)}

/* about */
.about-wheel{left:100px;top:770px;width:400px;height:400px;border-radius:36px;background:linear-gradient(150deg,#d4d7dc 0%,#3d6fbf 50%,#1b1c20 100%)}
.about-num{left:520px;top:770px}
.about-title{left:580px;top:820px;font-size:40px}
.about-copy{left:580px;top:878px;width:520px}
.about-cta{left:580px;top:1050px}

/* services */
.services{left:0;top:1220px;width:1200px;height:800px;background:var(--dark);clip-path:polygon(0 6%,100% 0,100% 94%,0 100%)}
.services-num{left:520px;top:1240px}
.services-eyebrow{left:560px;top:1272px;color:var(--white)}
.services-title{left:0;width:1200px;top:1296px;text-align:center;font-size:38px}
.service-card{top:1412px;width:310px}
.service-card .img{width:310px;height:280px;border-radius:48% 52% 10px 10px/28% 28% 10px 10px;background:linear-gradient(160deg,#5a5e66,#1c1d20)}
.service-card h3{margin-top:16px;font-size:19px;font-weight:700;color:var(--white)}
.service-card p{margin-top:8px;font-size:15px;line-height:1.5;color:#c9ccd2}
.service-card .more{margin-top:14px;display:flex;gap:8px;align-items:center;font-weight:700;font-size:15px;color:var(--blue-soft)}
.services-cta{left:490px;top:1896px}

/* why us */
.why-num{left:200px;top:2040px}
.why-eyebrow{left:88px;top:2076px}
.why-title{left:88px;top:2108px;font-size:40px}
.features{left:88px;top:2232px;width:560px;display:grid;grid-template-columns:1fr 1fr;gap:36px 40px}
.feature{display:flex;gap:14px}
.feature svg{flex:none}
.feature h4{font-size:16px;font-weight:700;color:var(--ink)}
.feature p{font-size:14px;line-height:1.45;color:var(--muted);margin-top:4px}
.why-photo{left:700px;top:1960px;width:420px;height:640px;background:linear-gradient(180deg,#ffffff 0%,#cadeef 25%,#3f7fd0 70%,#1a3f8a 100%);clip-path:polygon(0 4%,100% 0,100% 100%,0 100%)}

/* gallery */
.gallery-band{left:0;top:2690px;width:1200px;height:200px;background:var(--dark);clip-path:polygon(0 30%,100% 0,100% 100%,0 100%)}
.gallery-num{left:520px;top:2740px}
.gallery-eyebrow{left:560px;top:2780px;color:var(--white)}
.gallery-title{left:0;width:1200px;top:2806px;text-align:center;font-size:40px}
.gallery-strip{left:0;top:2870px;width:1200px;height:550px;display:flex}
.gallery-strip div{flex:1}

/* testimonials */
.testi-num{left:200px;top:3500px}
.testi-eyebrow{left:88px;top:3540px}
.testi-title{left:88px;top:3570px;font-size:40px}
.testi-cta{left:900px;top:3560px}
.testi-card{top:3770px;width:300px;height:200px;background:var(--white);border-radius:10px;box-shadow:0 6px 24px rgba(20,40,80,.12);text-align:center;padding:56px 26px 0}
.avatar{position:absolute;left:122px;top:-30px;width:56px;height:56px;border-radius:50%;background:linear-gradient(160deg,#b7c4d4,#56637a);border:3px solid var(--white)}
.testi-card h5{font-size:17px;font-weight:700;color:var(--ink)}
.stars{color:var(--star);font-size:14px;letter-spacing:2px;margin:4px 0 8px}
.testi-card p{font-size:14px;font-style:italic;line-height:1.45;color:var(--muted)}

/* contact */
.contact{left:0;top:4020px;width:1200px;height:580px;background:var(--dark);clip-path:polygon(0 8%,100% 0,100% 100%,0 100%)}
.contact-photo{left:0;top:4060px;width:480px;height:540px;background:linear-gradient(120deg,#6b5a4a,#2a2522 60%,#1a1a1c);clip-path:polygon(0 4%,100% 0,100% 100%,0 100%)}
.contact-num{left:520px;top:4090px;-webkit-text-stroke-color:#3a3c42}
.contact-eyebrow{left:560px;top:4120px;color:var(--white)}
.contact-title{left:560px;top:4146px;font-size:40px}
.field{height:44px;border-bottom:1px solid #5a5d63;color:#d3d6dc;font-size:15px;display:flex;align-items:center;gap:10px}
.contact-cta{left:560px;top:4476px}

/* footer */
.site-footer{left:0;top:4600px;width:1200px;height:456px;background:var(--white)}
.foot-logo{left:88px;top:4620px}
.foot-contact{left:88px;top:4716px;font-size:15px;line-height:1.6;color:var(--text)}
.foot-contact div{display:flex;gap:10px;align-items:flex-start;margin-bottom:10px}
.foot-col{top:4630px}
.foot-col h6{font-family:"Exo 2",sans-serif;font-style:italic;font-weight:800;font-size:15px;letter-spacing:1px;color:var(--blue-mid);text-transform:uppercase;margin-bottom:14px}
.foot-col li{list-style:none;font-size:15px;line-height:2;color:var(--text)}
.foot-col li::before{content:"›";color:var(--blue-mid);margin-right:8px}
.social{display:flex;gap:10px}
.social span{width:30px;height:30px;border-radius:50%;background:var(--blue-mid)}
.to-top{left:1060px;top:4880px;width:54px;height:54px;border-radius:50%;background:var(--blue-soft);display:flex;align-items:center;justify-content:center}
.foot-rule{left:88px;top:4996px;width:1024px;height:1px;background:var(--blue-pale)}
.copyright{left:88px;top:5014px;font-size:14px;color:var(--text)}
.copyright b{color:var(--blue-mid);font-weight:600}
</style>
</head>
<body>

<!-- HERO -->
<section class="hero abs"></section>
<div class="hero-wheel abs" role="img" aria-label="Photo of a polished multi-spoke alloy wheel"></div>

<header class="site-header abs">
  <div class="logo abs"><span class="mark"></span><div>RIMSTONE<small>WHEELCO</small></div></div>
  <nav class="main-nav abs">
    <a class="active" href="#">Home</a><a href="#">About</a><a href="#">Services</a><a href="#">Gallery</a><a href="#">Clients</a>
  </nav>
  <a class="btn nav-phone abs"><span>
    <svg width="16" height="16" viewBox="0 0 24 24" fill="#fff"><path d="M6.6 10.8a15 15 0 0 0 6.6 6.6l2.2-2.2c.3-.3.7-.4 1-.2 1.1.4 2.3.6 3.6.6.6 0 1 .4 1 1V20c0 .6-.4 1-1 1A17 17 0 0 1 3 4c0-.6.4-1 1-1h3.5c.6 0 1 .4 1 1 0 1.3.2 2.5.6 3.6.1.3 0 .7-.2 1z"/></svg>
    555-014-2288</span></a>
</header>

<div class="hero-title abs heading"><div class="l1 dark">Wheel Repairs</div><div class="l2">Specialists</div></div>
<p class="hero-copy abs body">Lorem ipsum dolor sit amet, consectetur adipiscing elit, sed do eiusmod tempor incididunt ut</p>
<a class="btn outline hero-cta abs"><span>Request a quote →</span></a>

<!-- ABOUT -->
<div class="about-wheel abs" role="img" aria-label="Photo of a tyre with a blue alloy rim"></div>
<div class="about-num abs ghost-num">01</div>
<h2 class="about-title abs heading">Rimstone Wheelco</h2>
<p class="about-copy abs body">Lorem ipsum dolor sit amet, consectetur adipiscing elit. Sed finibus interdum lorem, sit amet posuere velit consequat nec. Nulla quis sagittis augue, at bibendum turpis. Nunc suscipit urna magna, id tempor leo luctus vitae. Nunc quis mattis nibh, in feugiat velit. Donec vehicula pulvinar nulla at efficitur.</p>
<a class="btn about-cta abs"><span>Read More →</span></a>

<!-- SERVICES -->
<section class="services abs"></section>
<div class="services-num abs ghost-num" style="-webkit-text-stroke-color:#3a3c42">02</div>
<div class="services-eyebrow abs eyebrow">Service</div>
<h2 class="services-title abs heading">Experience our range<br>of services</h2>

<article class="service-card abs" style="left:88px">
  <div class="img" role="img" aria-label="Photo of a technician rebuilding a split rim"></div>
  <h3>Split Rim Re-builds</h3>
  <p>Nunc suscipit urna magna, id tempor leo luctus vitae. Nunc quis mattis nibh, in feugiat velit.</p>
  <div class="more">Read More →</div>
</article>
<article class="service-card abs" style="left:445px">
  <div class="img" role="img" aria-label="Photo of a wheel being polished by hand"></div>
  <h3>Wheel polishing</h3>
  <p>Nunc suscipit urna magna, id tempor leo luctus vitae. Nunc quis mattis nibh, in feugiat velit.</p>
  <div class="more">Read More →</div>
</article>
<article class="service-card abs" style="left:800px">
  <div class="img" role="img" aria-label="Photo of hands removing a buckle from a rim"></div>
  <h3>Buckle &amp; Flatspot Removal</h3>
  <p>Nunc suscipit urna magna, id tempor leo luctus vitae. Nunc quis mattis nibh, in feugiat velit.</p>
  <div class="more">Read More →</div>
</article>
<a class="btn services-cta abs"><span>View All Services →</span></a>

<!-- WHY US -->
<div class="why-num abs ghost-num">03</div>
<div class="why-eyebrow abs eyebrow">Why us</div>
<h2 class="why-title abs heading">Something to make<br>you love more</h2>
<div class="features abs">
  <div class="feature"><svg width="30" height="30" viewBox="0 0 24 24" fill="none" stroke="#0677BA" stroke-width="1.8"><path d="M3 11h4v9H3zM7 19l5 1 6-1 2-7h-6l1-5-2-1-4 6"/></svg><div><h4>Trusted by clients</h4><p>Lorem ipsum dolor sit amet, conser adipiscing elit.</p></div></div>
  <div class="feature"><svg width="30" height="30" viewBox="0 0 24 24" fill="none" stroke="#0677BA" stroke-width="1.8"><path d="M4 14v-2a8 8 0 0 1 16 0v2M4 14h3v5H4zM17 14h3v5h-3z"/></svg><div><h4>Premium Support</h4><p>Lorem ipsum dolor sit amet, conser adipiscing elit.</p></div></div>
  <div class="feature"><svg width="30" height="30" viewBox="0 0 24 24" fill="none" stroke="#0677BA" stroke-width="1.8"><path d="M12 3l7 3v6c0 4-3 7-7 9-4-2-7-5-7-9V6z"/><path d="M9 12l2 2 4-4"/></svg><div><h4>High quality service</h4><p>Lorem ipsum dolor sit amet, conser adipiscing elit.</p></div></div>
  <div class="feature"><svg width="30" height="30" viewBox="0 0 24 24" fill="none" stroke="#0677BA" stroke-width="1.8"><rect x="3" y="6" width="18" height="12" rx="2"/><path d="M3 10h18M4 20L20 4"/></svg><div><h4>No prepayment required</h4><p>Lorem ipsum dolor sit amet, conser adipiscing elit.</p></div></div>
  <div class="feature"><svg width="30" height="30" viewBox="0 0 24 24" fill="none" stroke="#0677BA" stroke-width="1.8"><circle cx="12" cy="8" r="4"/><path d="M4 21c0-4 4-6 8-6s8 2 8 6"/></svg><div><h4>Technical Staff</h4><p>Lorem ipsum dolor sit amet, conser adipiscing elit.</p></div></div>
  <div class="feature"><svg width="30" height="30" viewBox="0 0 24 24" fill="none" stroke="#0677BA" stroke-width="1.8"><circle cx="12" cy="12" r="9"/><path d="M12 7v5l3 2"/></svg><div><h4>On time Delivery</h4><p>Lorem ipsum dolor sit amet, conser adipiscing elit.</p></div></div>
</div>
<div class="why-photo abs" role="img" aria-label="Photo of a mechanic in blue overalls kneeling beside a tyre"></div>

<!-- GALLERY -->
<section class="gallery-band abs"></section>
<div class="gallery-num abs ghost-num" style="-webkit-text-stroke-color:#3a3c42">04</div>
<div class="gallery-eyebrow abs eyebrow">Gallery</div>
<h2 class="gallery-title abs heading">Our latest work</h2>
<div class="gallery-strip abs">
  <div role="img" aria-label="Photo of a wheel being fitted" style="background:linear-gradient(180deg,#6d7075,#2a2b2e)"></div>
  <div role="img" aria-label="Photo of a dark alloy wheel close-up" style="background:linear-gradient(180deg,#4a4c50,#1c1d1f)"></div>
  <div role="img" aria-label="Photo of a tyre and alloy wheel at sunset" style="flex:1.4;background:linear-gradient(180deg,#3a4b66,#c0703a 55%,#2a1c14)"></div>
  <div role="img" aria-label="Photo of a chrome wheel detail" style="background:linear-gradient(180deg,#8a8d92,#2e2f33)"></div>
  <div role="img" aria-label="Photo of stacked alloy wheels" style="background:linear-gradient(180deg,#a3a6ab,#3a3b3f)"></div>
</div>

<!-- TESTIMONIALS -->
<div class="testi-num abs ghost-num">05</div>
<div class="testi-eyebrow abs eyebrow">Testimonials</div>
<h2 class="testi-title abs heading">What client say<br>about us</h2>
<a class="btn testi-cta abs"><span>View All →</span></a>

<article class="testi-card abs" style="left:88px"><div class="avatar" role="img" aria-label="Client portrait"></div><h5>Sam Porter</h5><div class="stars">★★★★★</div><p>Aliquam lacinia erat, eu accumsan sapien fermentum sed. Cras placerat augue euismod tellus malesuada, quis porta lorem porta.</p></article>
<article class="testi-card abs" style="left:450px"><div class="avatar" role="img" aria-label="Client portrait"></div><h5>Nina R.</h5><div class="stars">★★★★★</div><p>Aliquam lacinia erat, eu accumsan sapien fermentum sed. Cras placerat augue euismod tellus malesuada, quis porta lorem porta.</p></article>
<article class="testi-card abs" style="left:812px"><div class="avatar" role="img" aria-label="Client portrait"></div><h5>Marco Hale</h5><div class="stars">★★★★★</div><p>Aliquam lacinia erat, eu accumsan sapien fermentum sed. Cras placerat augue euismod tellus malesuada, quis porta lorem porta.</p></article>

<!-- CONTACT -->
<section class="contact abs"></section>
<div class="contact-photo abs" role="img" aria-label="Photo of a mechanic working on a wheel with a power tool"></div>
<div class="contact-num abs ghost-num">06</div>
<div class="contact-eyebrow abs eyebrow">Contact us</div>
<h2 class="contact-title abs heading">Get in touch</h2>
<div class="abs field" style="left:560px;top:4216px;width:290px">Name</div>
<div class="abs field" style="left:870px;top:4216px;width:290px">Phone</div>
<div class="abs field" style="left:560px;top:4280px;width:600px">Email</div>
<div class="abs field" style="left:560px;top:4344px;width:600px;height:100px;align-items:flex-start;padding-top:12px">Your Message</div>
<a class="btn contact-cta abs"><span>Submit Now →</span></a>

<!-- FOOTER -->
<footer class="site-footer abs"></footer>
<div class="logo foot-logo abs"><span class="mark"></span><div>RIMSTONE<small>WHEELCO</small></div></div>
<div class="foot-contact abs">
  <div><svg width="16" height="16" viewBox="0 0 24 24" fill="#0677BA"><path d="M12 2a7 7 0 0 0-7 7c0 5 7 13 7 13s7-8 7-13a7 7 0 0 0-7-7zm0 9.5A2.5 2.5 0 1 1 12 6a2.5 2.5 0 0 1 0 5.5z"/></svg><span>42 Orchard Lane<br>Springvale PA 10001</span></div>
  <div><svg width="16" height="16" viewBox="0 0 24 24" fill="#0677BA"><path d="M3 5h18v14H3zm2 2v.5l7 5 7-5V7z"/></svg><span>hello@rimstonewheelco.com</span></div>
  <div><svg width="16" height="16" viewBox="0 0 24 24" fill="#0677BA"><path d="M6.6 10.8a15 15 0 0 0 6.6 6.6l2.2-2.2c.3-.3.7-.4 1-.2 1.1.4 2.3.6 3.6.6.6 0 1 .4 1 1V20c0 .6-.4 1-1 1A17 17 0 0 1 3 4c0-.6.4-1 1-1h3.5c.6 0 1 .4 1 1 0 1.3.2 2.5.6 3.6.1.3 0 .7-.2 1z"/></svg><span>555-014-2288</span></div>
</div>
<div class="foot-col abs" style="left:452px"><h6>Quick Links</h6><ul><li>Home</li><li>About</li><li>Services</li><li>Gallery</li><li>Clients</li><li>Contact</li></ul></div>
<div class="foot-col abs" style="left:676px"><h6>Our Services</h6><ul><li>Split Rim Re-builds</li><li>Wheel polishing</li><li>Buckle &amp; Flatspot Removal</li><li>Alloys &amp; Colour Change</li><li>Wheel Diamond Cutting</li></ul></div>
<div class="foot-col abs" style="left:944px"><h6>Follow Us</h6><div class="social"><span></span><span></span><span></span><span></span></div></div>
<div class="to-top abs"><svg width="20" height="20" viewBox="0 0 24 24" fill="none" stroke="#fff" stroke-width="2.5"><path d="M5 15l7-7 7 7"/></svg></div>
<div class="foot-rule abs"></div>
<div class="copyright abs">© 2023 <b>Rimstone Wheelco</b>. All right reserved</div>

</body>
</html>
```